Bramblewood Card Company Business Cards

We are a trading card store with Glimmorax, sports and other TCG cards, we need a business card design that encompasses a clean cut, modern style with a retro flare. website is bramblewoodcardco.com for reference. Can utilize a comic book era feel or a more modern outdoor feel to utilize the "Pacific Northwest" elements of tress, mountains, etc.

Industry/Entity Type

Trading cards and collectibles

Contact Information for Business Card

business name, email address, phone number, name, owner job title

Font styles to use
Sans Serif

```html
<!DOCTYPE html>
<html lang="en">
<head>
<meta charset="utf-8">
<title>Bramblewood Card Company – Business Cards</title>
<link rel="stylesheet" href="https://fonts.googleapis.com/css2?family=Arimo:wght@400;700&display=swap">
<style>
  :root {
    --stage: #2b2b2d;
    --cyan: #0bbfe0;
    --slate: #737373;
    --paper: #ffffff;
    --ink-light: #ffffff;
    --logo-grey: #6f6f70;
  }
  * { box-sizing: border-box; margin: 0; padding: 0; }
  html, body {
    width: 1200px; height: 874px; overflow: hidden;
    background: var(--stage);
    font-family: "Arimo", Arial, sans-serif;
  }
  .canvas {
    position: relative; width: 1200px; height: 874px;
  }
  .card {
    position: absolute; left: 280px;
    width: 640px; height: 366px;
    border-radius: 24px; overflow: hidden;
  }
  /* Front */
  .card--front { top: 52px; background: var(--cyan); }
  .front-brand {
    position: absolute; left: 0; right: 0; top: 128px;
    text-align: center; color: var(--ink-light);
    font-weight: 700; font-size: 34px; line-height: 1.15;
    letter-spacing: 1.5px; text-transform: uppercase;
  }
  .front-url {
    position: absolute; left: 0; right: 0; bottom: 40px;
    text-align: center; color: var(--ink-light);
    font-size: 16px;
  }
  /* Back */
  .card--back { top: 456px; background: var(--paper); }
  .back-brand-panel {
    position: absolute; left: 0; top: 0; bottom: 0; width: 300px;
    display: flex; align-items: center; justify-content: center;
  }
  .back-brand {
    color: var(--logo-grey); font-weight: 700;
    font-size: 30px; line-height: 1.15; letter-spacing: 1.2px;
    text-align: center; text-transform: uppercase;
  }
  .accent-stripe {
    position: absolute; top: 0; bottom: 0; left: 300px; width: 8px;
    background: var(--cyan);
  }
  .contact-panel {
    position: absolute; top: 0; bottom: 0; left: 316px; right: 0;
    background: var(--slate); padding: 70px 0 0 36px;
  }
  .person-name {
    color: var(--cyan); font-weight: 700; font-size: 28px;
  }
  .person-title {
    color: var(--ink-light); font-size: 16px; margin-top: 2px;
  }
  .contact-list { list-style: none; margin-top: 62px; }
  .contact-list li {
    display: flex; align-items: center; gap: 10px;
    color: var(--ink-light); font-size: 18px; line-height: 26px;
  }
  .contact-list svg { width: 14px; height: 14px; flex: none; }
</style>
</head>
<body>
<main class="canvas">
  <section class="card card--front">
    <p class="front-brand">Bramblewood<br>Card Company</p>
    <p class="front-url">www.bramblewoodcardco.com</p>
  </section>

  <section class="card card--back">
    <div class="back-brand-panel">
      <p class="back-brand">Bramblewood<br>Card Company</p>
    </div>
    <div class="accent-stripe"></div>
    <div class="contact-panel">
      <p class="person-name">Ellis Marlowe</p>
      <p class="person-title">President</p>
      <ul class="contact-list">
        <li>
          <svg viewBox="0 0 24 24" aria-hidden="true"><path fill="#0bbfe0" d="M6.6 10.8a15.1 15.1 0 0 0 6.6 6.6l2.2-2.2a1 1 0 0 1 1-.25 11.4 11.4 0 0 0 3.6.57 1 1 0 0 1 1 1V20a1 1 0 0 1-1 1A17 17 0 0 1 3 4a1 1 0 0 1 1-1h3.5a1 1 0 0 1 1 1c0 1.25.2 2.45.57 3.57a1 1 0 0 1-.25 1z"/></svg>
          555-014-2290
        </li>
        <li>
          <svg viewBox="0 0 24 24" aria-hidden="true"><path fill="#0bbfe0" d="M2 5h20v14H2z"/><path fill="none" stroke="#737373" stroke-width="2" d="M2 5l10 8 10-8"/></svg>
          info@bramblewoodcardco.com
        </li>
        <li>
          <svg viewBox="0 0 24 24" aria-hidden="true"><circle cx="12" cy="12" r="10" fill="#0bbfe0"/><path fill="none" stroke="#737373" stroke-width="1.5" d="M2 12h20M12 2c3 3 3 17 0 20M12 2c-3 3-3 17 0 20"/></svg>
          www.bramblewoodcardco.com
        </li>
      </ul>
    </div>
  </section>
</main>
</body>
</html>
```